Brell Stone Company Business Cards

Front and Back Business Card - logo and text setup - cool design. I need workable photoshop or illustrator files so I can setup each employee card with design that is created
Updates

Hi everyone, thank you for the great entries. Please no more white and blue cards - there are so many already - black and silver only now please. thanks!

Target Market(s)

Construction Industry - Facility Managers

Industry/Entity Type

Construction

Contact Information for Business Card

I really like contemporary simplistic looks - clean neat....not opposed to seeing some black backrounds

Requirements
Must have
• Logo/website address with design on front only - www.brellstone-example.com (logo attached)
• Back:
• Name/Title/Company Address/Phone/email address
Nice to have
• Cool design
Should not have
• Nothing gimmicky like Fire or Water - since we are a Fire Protection company - it has all been done

```html
<!DOCTYPE html>
<html lang="en">
<head>
<meta charset="utf-8">
<title>Brell Stone Company – Business Cards</title>
<link href="https://fonts.googleapis.com/css2?family=PT+Sans:wght@400;700&display=swap" rel="stylesheet">
<style>
  :root {
    --backdrop: #c9cccf;
    --card-black: #000000;
    --brand-red: #ff2323;
    --brand-blue: #0424a0;
    --ink-white: #ffffff;
  }
  * { margin: 0; padding: 0; box-sizing: border-box; }
  html, body {
    width: 1200px; height: 1193px; overflow: hidden;
    background: var(--backdrop);
    font-family: "PT Sans", Arial, sans-serif;
  }
  .canvas { position: relative; width: 1200px; height: 1193px; }
  .card {
    position: absolute; width: 873px; height: 499px;
    border-radius: 42px; overflow: hidden;
  }
  /* Contact side */
  .card--contact { left: 265px; top: 69px; background: var(--card-black); color: var(--ink-white); }
  .accent-bar { position: absolute; left: 0; top: 69px; width: 19px; height: 55px; background: var(--brand-red); }
  .person-name { position: absolute; left: 34px; top: 70px; font-size: 28px; font-weight: 700; line-height: 1; }
  .person-title { position: absolute; left: 34px; top: 105px; font-size: 25px; color: var(--brand-red); line-height: 1; }
  .wordmark-small {
    position: absolute; right: 46px; top: 76px;
    font-size: 58px; font-weight: 700; line-height: 1; color: var(--brand-red);
  }
  .contact-line { position: absolute; left: 34px; display: flex; align-items: center; gap: 12px; font-size: 22px; line-height: 1; }
  .contact-line svg { width: 20px; height: 20px; }
  .contact-line--phone { top: 258px; }
  .contact-line--email { top: 297px; }
  .address { position: absolute; left: 34px; top: 352px; font-size: 23px; line-height: 32px; }
  .footer-band { position: absolute; left: 0; bottom: 0; width: 873px; height: 66px; }
  .footer-url {
    position: absolute; right: 52px; bottom: 29px;
    font-size: 20px; letter-spacing: 1.5px; line-height: 1;
  }
  /* Brand side */
  .card--brand { left: 73px; top: 623px; background: var(--brand-blue); color: var(--ink-white); text-align: center; }
  .wordmark-large {
    position: absolute; left: 0; right: 0; top: 170px;
    font-size: 104px; font-weight: 700; line-height: 1;
  }
  .brand-url {
    position: absolute; left: 0; right: 0; top: 331px;
    font-size: 28px; letter-spacing: 6px; line-height: 1;
  }
</style>
</head>
<body>
<main class="canvas">
  <section class="card card--contact" aria-label="Business card, contact side">
    <div class="accent-bar"></div>
    <h1 class="person-name">Marla Quinlan</h1>
    <p class="person-title">President</p>
    <p class="wordmark-small">Brell Stone</p>

    <p class="contact-line contact-line--phone">
      <svg viewBox="0 0 24 24" aria-hidden="true"><path fill="var(--brand-red)" d="M6.6 10.8c1.4 2.8 3.8 5.1 6.6 6.6l2.2-2.2c.3-.3.7-.4 1-.2 1.1.4 2.3.6 3.6.6.6 0 1 .4 1 1V20c0 .6-.4 1-1 1C10.6 21 3 13.4 3 4c0-.6.4-1 1-1h3.5c.6 0 1 .4 1 1 0 1.3.2 2.5.6 3.6.1.3 0 .7-.2 1l-2.3 2.2z"/></svg>
      (555) 014-2273
    </p>
    <p class="contact-line contact-line--email">
      <svg viewBox="0 0 24 24" aria-hidden="true"><rect x="2" y="5" width="20" height="14" fill="var(--brand-red)"/><path d="M2 5l10 8 10-8M2 19l8-7M22 19l-8-7" stroke="#000" stroke-width="1.6" fill="none"/></svg>
      info@brellstone-example.com
    </p>
    <address class="address" style="font-style:normal">48 Harbor Point Road<br>Westbrook, NY 10555</address>

    <svg class="footer-band" viewBox="0 0 873 66" aria-hidden="true">
      <rect x="0" y="0" width="873" height="66" fill="var(--brand-blue)"/>
      <path d="M0 0 H 470 C 448 0 440 37 412 37 H 0 Z" fill="var(--brand-red)"/>
    </svg>
    <p class="footer-url">www.brellstone-example.com</p>
  </section>

  <section class="card card--brand" aria-label="Business card, brand side">
    <p class="wordmark-large">Brell Stone</p>
    <p class="brand-url">www.brellstone-example.com</p>
  </section>
</main>
</body>
</html>
```